Cafe menu flyer design

I need if possible A4 double sided menus. Two exemplars: first will contain breakfast menu on one side & refreshments menu on the other side, second exemplar will contain lunch menu on one side & refreshments menu on the other side. We do not need a description of the cafe or any history on these flyers, but design should reflect our surroundings and activities this area. We are located in main ski resort in UK-Cairngorm Mountains, right on the main ski road. The slopes are only 2 miles away from us. We are also very popular with wild life enthusiasts. Continues in design brief!

Cafe

```html
<!DOCTYPE html>
<html lang="en">
<head>
<meta charset="utf-8">
<title>Morag's @ Loch Ailie Cafe – Lunch &amp; Refreshments</title>
<link rel="stylesheet" href="https://fonts.googleapis.com/css2?family=Playfair+Display:ital,wght@1,900&family=Nunito+Sans:wght@700;800&display=swap">
<style>
  :root {
    --sky: #8fcdea;
    --mountain: #877790;
    --meadow: #7aa61f;
    --navy: #1d1b46;
    --ink: #111111;
    --white: #ffffff;
    --robin: #d8222a;
    --badge: #2f5da8;
  }
  * { margin: 0; padding: 0; box-sizing: border-box; }
  html, body { width: 1200px; height: 927px; overflow: hidden; }
  body { font-family: "Nunito Sans", Arial, sans-serif; }

  .flyer {
    position: relative;
    width: 1200px;
    height: 927px;
    background: var(--navy);
    overflow: hidden;
  }

  .scenery {
    position: absolute;
    inset: 0 0 auto 0;
    height: 282px;
    background: linear-gradient(180deg,
      var(--sky) 0%, var(--mountain) 22%, var(--mountain) 78%,
      var(--meadow) 80%, var(--meadow) 100%);
  }

  .cafe-name {
    position: absolute;
    left: 68px;
    top: 108px;
    font-family: "Playfair Display", Georgia, serif;
    font-style: italic;
    font-weight: 900;
    font-size: 76px;
    line-height: 1;
    color: var(--ink);
    letter-spacing: 0.5px;
  }
  .cafe-address {
    position: absolute;
    left: 497px;
    top: 192px;
    font-weight: 800;
    font-size: 16px;
    color: var(--ink);
  }

  .social {
    position: absolute;
    left: 1040px;
    top: 74px;
    width: 120px;
    text-align: center;
    color: var(--white);
    font-weight: 800;
    font-size: 15px;
    line-height: 18px;
  }
  .social-square {
    display: block;
    width: 100px;
    height: 100px;
    margin: 0 auto 6px;
    background: var(--badge);
    border-radius: 14px;
  }

  .menu-column {
    position: absolute;
    color: var(--white);
    font-weight: 800;
    font-size: 16.5px;
    line-height: 19.8px;
  }
  .menu-column.lunch { left: 70px; top: 303px; width: 560px; }
  .menu-column.refreshments { left: 692px; top: 305px; width: 470px; line-height: 21.15px; }

  .heading {
    font-size: inherit;
    font-weight: 800;
    line-height: inherit;
  }
  .line { display: flex; }
  .line .item { flex: none; }
  .lunch .line .item { width: 433px; }
  .refreshments .line .item { width: 400px; }
  .line .price { flex: none; }
  .indent-toastie { padding-left: 203px; }
  .indent-panini { padding-left: 203px; }
  .indent-chips { padding-left: 193px; }

  .fillings {
    display: grid;
    grid-template-columns: 286px auto;
    margin-top: 6px;
  }
  .fillings .sub { padding-left: 23px; }

  .gap { height: 12px; }

  .note {
    padding-left: 180px;
    width: 540px;
  }
  .wrap { padding-left: 6px; }

  .robin-area {
    position: absolute;
    left: 38px;
    top: 763px;
    width: 206px;
    height: 164px;
    background: var(--robin);
  }
</style>
</head>
<body>
<main class="flyer">
  <div class="scenery" role="img" aria-label="Mountain landscape with sky, clouds and green treeline"></div>

  <h1 class="cafe-name">Morag's @ Loch Ailie Cafe</h1>
  <p class="cafe-address">Strathbeg, Ardnish, PH30 4QX. Tel:01234567890</p>

  <div class="social"><span class="social-square"></span>Like us on Socialbook!</div>

  <div class="robin-area" role="img" aria-label="Red bird illustration"></div>

  <section class="menu-column lunch">
    <h2 class="heading">LUNCH MENU 12-4PM</h2>
    <div class="line"><span class="item">Soup of the day, served with brown roll &amp; butter</span><span class="price">£3.75</span></div>
    <div class="line"><span class="item">Freshly made toasties: one filling</span><span class="price">£3.20</span></div>
    <div class="line"><span class="item indent-toastie">two fillings</span><span class="price">£4.20</span></div>
    <div class="fillings">
      <span>Sundried tomato,pesto and</span><span>Cheese and ham</span>
      <span class="sub">Mozzarella cheese</span><span>Cheese and onion</span>
      <span>Mozzarella and salami</span><span>Cheese and tomato</span>
    </div>
    <div class="gap"></div>
    <div>!Paninis with fillings as above coming soon!</div>
    <div class="line"><span class="item indent-panini">One filling</span><span class="price">£4.20</span></div>
    <div class="line"><span class="item indent-panini">Two filling</span><span class="price">£5.20</span></div>
    <div>Local butchers beef burger meal,served with</div>
    <div class="line"><span class="item">chips and salad</span><span class="price">£7.95</span></div>
    <div>Home made chicken fillet burger meal, served</div>
    <div class="line"><span class="item">with chips and salad</span><span class="price">£7.95</span></div>
    <div class="line"><span class="item">Burger in a bun(on its own)</span><span class="price">£4.20</span></div>
    <div class="line"><span class="item">Pies assorted</span><span class="price">£2.50</span></div>
    <div class="line"><span class="item">Pie with beans</span><span class="price">£3.50</span></div>
    <div class="line"><span class="item">Pie with chips</span><span class="price">£5.00</span></div>
    <div class="line"><span class="item">Pie with beans and chips</span><span class="price">£6.00</span></div>
    <div class="line"><span class="item">Basket of chips</span><span class="price">£3.50</span></div>
    <div class="line"><span class="item indent-chips">Chip butty</span><span class="price">£2.00</span></div>
    <div class="line"><span class="item indent-chips">Chips &amp; beans</span><span class="price">£4.50</span></div>
    <div class="line"><span class="item indent-chips">Chips &amp; cheese</span><span class="price">£4.50</span></div>
    <div class="line"><span class="item indent-chips">Rolls with assorted</span></div>
    <div class="line"><span class="item indent-chips">cold fillings</span><span class="price">£2.20 - £3.20</span></div>
    <p class="note">Gluten free bread and cakes available- ask staff! At the height of the season evening meals available. Ask staff for more info.</p>
  </section>

  <section class="menu-column refreshments">
    <h2 class="heading">REFRESHMENTS</h2>
    <div class="line"><span class="item">Tea</span><span class="price">£1.50</span></div>
    <div>Filter Coffee, decaf coffee, plain hot chocolate</div>
    <div>£2.00</div>
    <div class="line"><span class="item">Selection of herbal teas</span><span class="price">£2.00</span></div>
    <div class="line"><span class="item">Specialty black tea with your choice of syrup</span><span class="price">£2.50</span></div>
    <div class="wrap">strawberry, raspberry, apple &amp; mint tea</div>
    <div class="line"><span class="item">Assorted premium “Leaf Hound” teas</span><span class="price">£2.50</span></div>
    <div class="line"><span class="item">Hot chocolate with cream</span><span class="price">£2.20</span></div>
    <div class="line"><span class="item">Hot chocolate with marsh mallows</span><span class="price">£2.20</span></div>
    <div class="line"><span class="item">Hot chocolate with cream &amp; marsh mallows</span><span class="price">£2.20</span></div>
    <div class="line"><span class="item">Hot chocolate with brandy</span><span class="price">£3.50</span></div>
    <div>Hot chocolate with brandy, marsh mallows &amp;</div>
    <div class="line"><span class="item">cream</span><span class="price">£4.50</span></div>
    <div class="line"><span class="item">Cafe Latte/Cappucino</span><span class="price">£2.50</span></div>
    <div class="line"><span class="item">Squirrel Latte</span><span class="price">£3.50</span></div>
    <div class="line"><span class="item">Chocolate Latte</span><span class="price">£3.50</span></div>
    <div class="line"><span class="item">Cinnamon Latte</span><span class="price">£3.50</span></div>
    <div class="line"><span class="item">Caramel Latte</span><span class="price">£3.50</span></div>
    <div class="line"><span class="item">Butterscotch Latte</span><span class="price">£3.50</span></div>
    <div class="line"><span class="item">Gingerbread Latte</span><span class="price">£3.50</span></div>
    <div class="line"><span class="item">Mocha</span><span class="price">£3.50</span></div>
    <div class="line"><span class="item">Glass of milk</span><span class="price">£1.20</span></div>
    <div class="line"><span class="item">Milkshakes</span><span class="price">£2.00</span></div>
    <div class="line"><span class="item">Still or Sparkling water</span><span class="price">£1.80</span></div>
    <div class="line"><span class="item">Cans of juice</span><span class="price">£1.60</span></div>
    <div class="line"><span class="item">Cartons of juice</span><span class="price">£1.30</span></div>
  </section>
</main>
</body>
</html>
```